Software Development Consulting Company Needs Business Card Design

We need a new business card design for our consultants at Kestrel Works (kestrelworks.example). We are a small firm that provides high-end software development and methodology consulting to medium to large enterprise IT organizations.

Our logo uses Futura for the font and we would like to stick with navy blue and canary yellow for the logo colors. Attached are normal and reversed versions of our logos in illustrator format.
Updates

Hi Everyone, Thank yo very much for your amazing design ideas. I have created a poll for this project and our employees will be voting on the design they wish to use. We will be making a decision this Wednesday (October 22nd). Thanks again, Dale Hartwick

Industry/Entity Type

Business

```html
<!DOCTYPE html>
<html lang="en">
<head>
<meta charset="utf-8">
<title>Kestrel Works — Business Card</title>
<link href="https://fonts.googleapis.com/css2?family=Open+Sans:wght@400;600&display=swap" rel="stylesheet">
<style>
  :root {
    --navy: #1c4a72;
    --canary: #f7e600;
    --paper: #ffffff;
    --ink-muted: #4a5560;
    --stage: #e9e9ee;
  }
  * { box-sizing: border-box; margin: 0; padding: 0; }
  html, body { width: 1200px; height: 980px; overflow: hidden; background: var(--stage); }
  body { position: relative; font-family: "Open Sans", sans-serif; color: var(--navy); }

  .card {
    position: absolute;
    background: var(--paper);
    border-radius: 24px;
    overflow: hidden;
    box-shadow: 0 2px 6px rgba(0,0,0,0.12);
  }
  .card--back  { left: 520px; top: 80px;  width: 600px; height: 343px; }
  .card--front { left: 80px;  top: 500px; width: 640px; height: 366px; }

  .brand { display: flex; align-items: center; gap: 10px; }
  .brand__dot { width: 12px; height: 12px; border-radius: 50%; background: var(--canary); border: 2px solid var(--navy); }
  .brand__name { font-weight: 600; color: var(--navy); letter-spacing: 0.12em; text-transform: uppercase; }

  .card--back .brand { position: absolute; left: 0; right: 0; top: 108px; justify-content: center; }
  .card--back .brand__name { font-size: 38px; }
  .card--back .web { position: absolute; left: 0; right: 0; top: 200px; text-align: center; font-size: 20px; letter-spacing: 0.14em; color: var(--ink-muted); }

  .card--front .brand { position: absolute; left: 36px; top: 34px; }
  .card--front .brand__name { font-size: 30px; }

  .wave { position: absolute; inset: 0; width: 100%; height: 100%; }

  .band-id { position: absolute; left: 26px; top: 184px; color: var(--paper); }
  .band-id .name { font-size: 20px; font-weight: 600; line-height: 1.2; }
  .band-id .title { font-size: 13px; }

  .contact { position: absolute; right: 34px; top: 168px; text-align: right; }
  .contact .name { font-size: 24px; font-weight: 600; color: var(--navy); line-height: 1.1; }
  .contact .title { font-size: 15px; color: var(--ink-muted); margin-bottom: 12px; }
  .contact .line { font-size: 15px; color: var(--ink-muted); line-height: 1.5; display: flex; justify-content: flex-end; align-items: center; gap: 6px; }
  .contact svg { width: 14px; height: 14px; }
</style>
</head>
<body>
  <section class="card card--back" aria-label="Card back">
    <div class="brand"><span class="brand__dot"></span><span class="brand__name">Kestrel Works</span></div>
    <p class="web">www.kestrelworks.example</p>
  </section>

  <section class="card card--front" aria-label="Card front">
    <svg class="wave" viewBox="0 0 640 366" preserveAspectRatio="none" aria-hidden="true">
      <path d="M0 104 C150 100 200 250 340 316 C420 352 530 356 640 352" fill="none" stroke="var(--canary)" stroke-width="7"/>
      <path d="M0 114 C145 112 190 258 332 324 C412 358 530 364 640 362 L640 366 L0 366 Z" fill="var(--navy)"/>
    </svg>

    <div class="brand"><span class="brand__dot"></span><span class="brand__name">Kestrel Works</span></div>

    <div class="band-id">
      <p class="name">Your Name</p>
      <p class="title">Title</p>
    </div>

    <div class="contact">
      <p class="name">Your Name</p>
      <p class="title">Title</p>
      <p class="line">
        <svg viewBox="0 0 16 16" aria-hidden="true"><circle cx="8" cy="8" r="7" fill="none" stroke="var(--navy)" stroke-width="1.6"/><path d="M5.5 4.5l1.5 1.5-1 1c.6 1.2 1.5 2.1 2.8 2.8l1-1 1.5 1.5-1 1.2c-2.6-.6-4.6-2.6-5.3-5.3z" fill="var(--navy)"/></svg>
        000-555-0142
      </p>
      <p class="line">
        <svg viewBox="0 0 16 16" aria-hidden="true"><rect x="1.5" y="3.5" width="13" height="9" rx="1" fill="var(--navy)"/><path d="M2 4l6 5 6-5" fill="none" stroke="#fff" stroke-width="1.3"/></svg>
        info@kestrelworks.example
      </p>
      <p class="line">Harbor City + Lakemont</p>
    </div>
  </section>
</body>
</html>
```